Business Card Design needed for start up company Halvora

In need of a new business card designed for a start up company based in Sydney, Halvora is a new start up innovative Company, our mission it to make property accessible for everyday Australian and to become the leading Real Estate platform in Australia. We want it to be fresh and clean.

Industry/Entity Type

Financial

Contact Information for Business Card

Section for Name
Section for Title

HALVORA - The Strength of Pooling
Mobile:
Direct:

Font styles to use
Sans Serif

Colors
33a6d7
0692cd
0255a3
ffffff

Requirements
Must have
• Logo, all business card details

```html
<!DOCTYPE html>
<html lang="en">
<head>
<meta charset="utf-8">
<title>Halvora Business Card</title>
<link rel="stylesheet" href="https://fonts.googleapis.com/css2?family=Open+Sans:wght@400;600;700;800&display=swap">
<style>
  :root {
    --sky: #33a6d7;
    --ocean: #0692cd;
    --navy: #0255a3;
    --white: #ffffff;
    --ink: #4a4a4a;
    --stage: #e4e6e9;
  }
  * { margin: 0; padding: 0; box-sizing: border-box; }
  html, body { width: 1200px; height: 1000px; overflow: hidden; }
  body {
    background: var(--stage);
    font-family: "Open Sans", Arial, sans-serif;
    position: relative;
  }
  .card {
    position: absolute;
    left: 250px;
    width: 700px;
    height: 400px;
    background: var(--white);
    border-radius: 22px;
    overflow: hidden;
    box-shadow: 0 10px 30px rgba(0,0,0,0.12);
  }
  .card--front { top: 60px; }
  .card--back { top: 540px; }

  /* Front */
  .name-tab {
    position: absolute; left: -18px; top: 38px;
    width: 36px; height: 36px; border-radius: 50%;
    background: var(--sky);
  }
  .identity { position: absolute; left: 44px; top: 34px; }
  .identity__name {
    font-size: 27px; font-weight: 800; color: var(--navy);
    text-transform: uppercase; letter-spacing: 0.5px; line-height: 1.1;
  }
  .identity__title { font-size: 20px; color: var(--sky); font-weight: 600; }

  .contacts { position: absolute; left: 44px; top: 130px; list-style: none; }
  .contacts__item {
    display: flex; align-items: flex-start; gap: 12px;
    font-size: 17px; color: var(--ink); line-height: 1.35; margin-bottom: 6px;
  }
  .contacts__icon { width: 16px; height: 16px; margin-top: 3px; flex: none; }

  .brand {
    position: absolute; display: flex; align-items: center;
  }
  .brand__dot { border-radius: 50%; background: var(--sky); flex: none; }
  .brand__name { font-weight: 800; color: var(--navy); line-height: 1; letter-spacing: 1px; }

  .brand--front { right: 44px; bottom: 78px; gap: 12px; }
  .brand--front .brand__dot { width: 64px; height: 64px; }
  .brand--front .brand__name { font-size: 46px; }

  .web-band { position: absolute; left: 300px; bottom: 0; width: 280px; height: 48px; }
  .web-band__text {
    position: absolute; left: 320px; bottom: 12px;
    font-size: 18px; color: var(--white); font-weight: 600;
  }

  /* Back */
  .brand--back { left: 50%; top: 120px; transform: translateX(-50%); gap: 18px; }
  .brand--back .brand__dot { width: 110px; height: 110px; }
  .brand--back .brand__name { font-size: 92px; }
  .tagline {
    position: absolute; left: 0; right: 0; top: 270px; text-align: center;
    font-size: 16px; letter-spacing: 7px; color: var(--ink); text-transform: uppercase;
  }
</style>
</head>
<body>

<section class="card card--front" aria-label="Business card front">
  <span class="name-tab"></span>
  <div class="identity">
    <div class="identity__name">Dana Werner</div>
    <div class="identity__title">Director</div>
  </div>

  <ul class="contacts">
    <li class="contacts__item">
      <svg class="contacts__icon" viewBox="0 0 16 16"><path d="M8 1C5.2 1 3.2 3.1 3.2 5.8 3.2 9.4 8 15 8 15s4.8-5.6 4.8-9.2C12.8 3.1 10.8 1 8 1zm0 6.6a1.8 1.8 0 1 1 0-3.6 1.8 1.8 0 0 1 0 3.6z" fill="var(--sky)"/></svg>
      <span>18 Harbour Lane,<br>Sydney, 2000</span>
    </li>
    <li class="contacts__item">
      <svg class="contacts__icon" viewBox="0 0 16 16"><path d="M3.6 1.5l2.2 2.8-1.3 1.6c.9 2 2.5 3.6 4.6 4.6l1.6-1.3 2.8 2.2-1.3 2.4C7 13.6 2.4 9 2.2 3z" fill="var(--sky)"/></svg>
      <span>000 418 260 731</span>
    </li>
    <li class="contacts__item">
      <svg class="contacts__icon" viewBox="0 0 16 16"><rect x="4" y="1" width="8" height="14" rx="1.5" fill="none" stroke="var(--sky)" stroke-width="1.6"/><circle cx="8" cy="12.5" r="0.9" fill="var(--sky)"/></svg>
      <span>000 904 5521</span>
    </li>
    <li class="contacts__item">
      <svg class="contacts__icon" viewBox="0 0 16 16"><rect x="1" y="3" width="14" height="10" rx="1" fill="var(--sky)"/><path d="M1.5 3.8L8 9l6.5-5.2" fill="none" stroke="var(--white)" stroke-width="1.3"/></svg>
      <span>dana@halvora-pool.com</span>
    </li>
  </ul>

  <div class="brand brand--front">
    <span class="brand__dot"></span>
    <span class="brand__name">HALVORA</span>
  </div>

  <svg class="web-band" viewBox="0 0 280 48" preserveAspectRatio="none">
    <polygon points="0,0 120,0 80,48 0,48" fill="var(--sky)"/>
    <polygon points="120,0 280,0 280,48 80,48" fill="var(--navy)"/>
  </svg>
  <span class="web-band__text">www.halvora-pool.com</span>
</section>

<section class="card card--back" aria-label="Business card back">
  <div class="brand brand--back">
    <span class="brand__dot"></span>
    <span class="brand__name">HALVORA</span>
  </div>
  <p class="tagline">The Strength of Pooling</p>
</section>

</body>
</html>
```